Web Design Project

We need a web design company for a company based in London. We are an online minicab booking service that produces real time quotes on cab journey for consumers. Our colours are currently red and yellow, but do not need to stay that way; it's open to interpretation. Please avoid yellow and black as a colour combination. Our current site is: www.rovelink.co.uk We are looking for a new site to be user-friendly and easy to use, but more polished and professional looking, without using it usability and simplicity. We need to keep the booking capability on each page and it needs to draw in the user's eye. We need a site that is reliable and easy to use, but also fun.

Main objective: keep it simple, like it is now, but polish it up some. Also, we need to be able to add more content to it. And, we will also be adding a login capability for return users.

Target Market(s)

Internet-savvy people aged 18 and older.

Industry/Entity Type

It Company

Requirements
Must have
• Must have the booking widget. However, it doesn't have to be as large as it is now. We are actually thinking to split it over two pages. We will add a few options to the booking widget, such as another via option. The booking widget must be the most noticeable feature on the page. Sans serif font, please.
Should not have
• Should not be too busy and distracting. Please do not use any images of traditional taxis, ie. black cabs from London or yellow cabs from NYC. Our cars do not resemble these and our business cannot be associated with these images.

```html
<!DOCTYPE html>
<html lang="en">
<head>
<meta charset="utf-8">
<title>Rovelink – Book a Cab</title>
<link rel="stylesheet" href="https://fonts.googleapis.com/css2?family=Open+Sans:ital,wght@0,300;0,400;0,600;1,400&family=Oswald:wght@300;400&family=Questrial&display=swap">
<style>
:root{
  --header-top:#2f7cc0;
  --header-bottom:#3eaad9;
  --nav:#1f6aaa;
  --nav-active:#7fd3f7;
  --brand:#2170b5;
  --brand-dark:#123f80;
  --panel-top:#f4f4f4;
  --panel-bottom:#d6d6d6;
  --field-border:#9a9a9a;
  --placeholder:#9a9a9a;
  --ink:#222;
  --muted:#8c8c8c;
  --white:#fff;
  --rule:#c9c9c9;
  --hero-top:#24477f;
  --hero-mid:#1c2a45;
  --hero-bottom:#0c111d;
}
*{box-sizing:border-box;margin:0;padding:0}
html,body{width:1111px;height:1200px;overflow:hidden;background:var(--white)}
body{font-family:"Open Sans",Arial,sans-serif;color:var(--ink)}
.page{position:relative;width:1000px;height:1080px;transform:scale(1.111);transform-origin:0 0}
.abs{position:absolute}

/* header */
.site-header{left:0;top:0;width:1000px;height:144px;background:linear-gradient(180deg,var(--header-top),var(--header-bottom))}
.brand-name{left:37px;top:46px;font-family:"Open Sans",sans-serif;font-weight:400;font-size:46px;color:var(--white);letter-spacing:-.5px}
.driver-invite{right:20px;top:24px;font-size:15px;color:var(--white)}
.driver-invite a{color:var(--white);font-weight:600;text-decoration:underline;margin-left:6px}
.call-line{right:17px;top:62px;font-family:"Questrial",sans-serif;font-size:18px;color:var(--white)}
.phone{right:17px;top:92px;font-family:"Oswald",sans-serif;font-size:33px;color:var(--white);letter-spacing:.5px}

/* nav */
.main-nav{left:0;top:144px;width:1000px;height:60px;background:var(--nav)}
.nav-item{top:18px;font-family:"Oswald",sans-serif;font-size:19px;color:var(--white);text-transform:uppercase}
.nav-item.active{color:var(--nav-active)}
.social-slot{top:12px;width:36px;height:36px;border-radius:5px;background:var(--white)}

/* hero image placeholder */
.hero-photo{left:0;top:204px;width:514px;height:395px;
  background:linear-gradient(180deg,var(--hero-top) 0%,var(--hero-mid) 50%,var(--hero-bottom) 100%)}

/* booking form */
.booking{left:514px;top:204px;width:486px;height:395px;background:linear-gradient(180deg,var(--panel-top),var(--panel-bottom))}
.booking-title{left:10px;top:5px;font-family:"Questrial",sans-serif;font-size:18px;color:var(--brand)}
.label{font-family:"Questrial",sans-serif;font-size:14px;color:var(--ink)}
.field{height:29px;border:1px solid var(--field-border);background:var(--white);font-size:12px;font-style:italic;color:var(--placeholder);padding:6px 5px;white-space:nowrap;overflow:hidden}
.field.area{height:77px}
.field-icon{position:absolute;right:4px;top:3px}
.select-arrow{position:absolute;right:0;top:0;width:25px;height:27px;border-left:1px solid var(--field-border);background:var(--white)}
.select-arrow::after{content:"";position:absolute;left:7px;top:11px;border:6px solid transparent;border-top:7px solid #111;border-bottom:0}
.check{width:14px;height:14px;border:1px solid #aaa;background:linear-gradient(#fff,#ddd)}
.quote-btn{left:247px;top:337px;width:228px;height:38px;border-radius:19px;background:var(--brand-dark);color:var(--white);font-family:"Questrial",sans-serif;font-size:13px;text-align:center;line-height:38px;white-space:nowrap}

/* lower left */
.pill-heading{left:0;background:var(--brand);color:var(--white);font-family:"Oswald",sans-serif;border-radius:0 30px 30px 0}
.steps-heading{top:617px;width:339px;height:57px;padding:4px 0 0 19px}
.steps-heading .big{font-size:22px;line-height:28px}
.steps-heading .small{font-size:14px;font-weight:300;margin-left:67px;line-height:18px}
.step{left:35px;font-family:"Oswald",sans-serif;font-weight:400;font-size:16px;color:var(--ink);display:flex;align-items:center;gap:9px}
.why-heading{top:784px;width:123px;height:41px;font-size:22px;padding:5px 0 0 19px}
.reason{left:21px;width:585px;font-size:12px;line-height:17px;color:#333}
.reason h3{font-weight:400;font-size:12px;color:var(--brand);margin-bottom:1px}

.divider{left:619px;top:615px;width:1px;height:370px;background:var(--rule)}

/* community */
.stories-title{left:646px;top:628px;font-family:"Questrial",sans-serif;font-size:16px;color:var(--brand)}
.story{left:642px;top:670px;width:335px;font-size:12.4px;font-style:italic;line-height:16.85px;color:var(--muted);text-align:justify}
.mini-btn{top:881px;height:23px;border:1px solid #b7c2d8;border-radius:3px;background:linear-gradient(#f7f8fb,#e3e7f0);font-size:11px;color:#3b5284;padding:3px 6px}
.likes{left:644px;top:914px;font-size:11px;color:#333;display:flex;align-items:center;gap:5px}
.likes i{display:block;width:11px;height:11px;background:#5b6f9f}
.story-btn{left:700px;top:958px;width:230px;height:28px;border-radius:14px;background:var(--brand);color:var(--white);font-size:16px;text-align:center;line-height:28px}

/* footer */
.site-footer{left:0;top:1017px;width:1000px;height:63px;background:var(--nav);color:var(--white);font-size:16px;text-align:center;padding-top:21px}
</style>
</head>
<body>
<div class="page">

  <header class="site-header abs">
    <div class="brand-name abs">ROVELINK.CO.UK</div>
    <div class="driver-invite abs">Are you a taxi driver or a company ? <a>JOIN US HERE</a></div>
    <div class="call-line abs">Queries? Feel Free to Call Us</div>
    <div class="phone abs">020 3946 1175</div>
  </header>

  <nav class="main-nav abs">
    <span class="nav-item abs active" style="left:21px">Home</span>
    <span class="nav-item abs" style="left:138px">Rovelink Miles</span>
    <span class="nav-item abs" style="left:311px">Join Us</span>
    <span class="nav-item abs" style="left:440px">About Us</span>
    <span class="nav-item abs" style="left:582px">Contact</span>
    <span class="social-slot abs" style="left:863px" aria-label="Social link"></span>
    <span class="social-slot abs" style="left:907px" aria-label="Social link"></span>
    <span class="social-slot abs" style="left:950px" aria-label="Social link"></span>
  </nav>

  <div class="hero-photo abs" role="img" aria-label="Photo of rows of cabs at night"></div>

  <section class="booking abs">
    <h2 class="booking-title abs" style="font-weight:400">BOOK A CAB</h2>

    <span class="label abs" style="left:12px;top:36px">Pick Me from</span>
    <span class="label abs" style="left:262px;top:36px">Drop Me At</span>
    <div class="field abs" style="left:12px;top:58px;width:210px">e.g pick up address or postal code</div>
    <div class="field abs" style="left:263px;top:58px;width:210px">e.g pick up address or postal code</div>

    <span class="label abs" style="left:12px;top:98px">Pick Up Date</span>
    <span class="label abs" style="left:141px;top:98px">Time</span>
    <span class="label abs" style="left:274px;top:98px">Just Pick up me in</span>
    <div class="field abs" style="left:12px;top:118px;width:115px">MM/DD/YYYY
      <svg class="field-icon" width="22" height="22" viewBox="0 0 22 22"><rect x="1" y="3" width="20" height="18" fill="#fff" stroke="#888"/><rect x="1" y="3" width="20" height="4" fill="#888"/><g fill="#999"><rect x="4" y="9" width="3" height="3"/><rect x="9" y="9" width="3" height="3"/><rect x="14" y="9" width="3" height="3"/><rect x="4" y="14" width="3" height="3"/><rect x="9" y="14" width="3" height="3"/><rect x="14" y="14" width="3" height="3"/></g></svg>
    </div>
    <div class="field abs" style="left:142px;top:118px;width:115px">Hrs/Mins
      <svg class="field-icon" width="22" height="22" viewBox="0 0 22 22"><circle cx="11" cy="11" r="9" fill="#fff" stroke="#888" stroke-width="2"/><path d="M11 5v6l4 2" stroke="#666" stroke-width="1.6" fill="none"/></svg>
    </div>
    <div class="field abs" style="left:272px;top:118px;width:152px">---------10 Mins---------<span class="select-arrow"></span></div>

    <span class="label abs" style="left:12px;top:158px">Passengers</span>
    <div class="field abs" style="left:12px;top:181px;width:114px">-----Adults------<span class="select-arrow"></span></div>
    <div class="field abs" style="left:142px;top:181px;width:114px">------Bags-------<span class="select-arrow"></span></div>
    <span class="check abs" style="left:272px;top:187px"></span>
    <span class="label abs" style="left:291px;top:185px">Round Trip</span>
    <span class="check abs" style="left:381px;top:187px"></span>
    <span class="label abs" style="left:400px;top:185px">Extras</span>

    <span class="label abs" style="left:12px;top:218px">Name</span>
    <span class="label abs" style="left:243px;top:218px">Comments</span>
    <div class="field abs" style="left:12px;top:238px;width:210px">enter you name</div>
    <div class="field area abs" style="left:245px;top:238px;width:227px;white-space:normal">type any special instructions here</div>

    <span class="label abs" style="left:12px;top:278px">Mobile</span>
    <div class="field abs" style="left:12px;top:298px;width:210px">enter you mobile number</div>

    <span class="label abs" style="left:12px;top:338px">Email</span>
    <div class="field abs" style="left:12px;top:358px;width:210px">enter you email address</div>

    <div class="quote-btn abs">GET YOUR NO OBLIGATION QUOTE</div>
  </section>

  <div class="pill-heading steps-heading abs">
    <div class="big">AS EASY AS OPENING THE CAB'S DOOR</div>
    <div class="small">Its free, dependable and with no obligation</div>
  </div>
  <div class="step abs" style="top:680px"><svg width="14" height="14" viewBox="0 0 14 14"><circle cx="7" cy="7" r="6" fill="#eee" stroke="#aaa"/><path d="M5.5 4l4 3-4 3z" fill="#666"/></svg>Enter your route</div>
  <div class="step abs" style="top:712px"><svg width="14" height="14" viewBox="0 0 14 14"><circle cx="7" cy="7" r="6" fill="#eee" stroke="#aaa"/><path d="M5.5 4l4 3-4 3z" fill="#666"/></svg>Quickly compare taxi fares</div>
  <div class="step abs" style="top:744px"><svg width="14" height="14" viewBox="0 0 14 14"><circle cx="7" cy="7" r="6" fill="#eee" stroke="#aaa"/><path d="M5.5 4l4 3-4 3z" fill="#666"/></svg>Get your travel confirmed on your phone by SMS.</div>

  <div class="pill-heading why-heading abs">WHY US ?</div>
  <div class="reason abs" style="top:835px"><h3>PRICE</h3>Rovelink guarantees that you get the best deal for your travel, as you get quotes from several cab companies.</div>
  <div class="reason abs" style="top:902px"><h3>NO FEES</h3>There's absolutely no cost for you to use our service.</div>
  <div class="reason abs" style="top:952px"><h3>COVERAGE</h3>Rovelink has the largest database of licensed minicab operators. You can use Rovelink wherever you are in greater London.</div>

  <div class="divider abs"></div>

  <h2 class="stories-title abs" style="font-weight:400">THE BEST STORIES FROM OUR COMMUNITY</h2>
  <p class="story abs">I recently hit London for a girlie night on the town with my bestie. After a little too much champagne, we had a stupid argument and decided to leave the club early. In the cab on our way home, we didn’t say one word to each other. The driver who could sense we were both upset however, had other plans. He randomly started singing the Velvet Larks’ Neon Lullaby! My best friend and I were in shock, we looked at each other and couldn’t stop laughing! The remainder of the journey consisted of us all belting out Larks classics, in between fits of laughter. We were so disappointed when we arrived home as we wanted to continue the fun, we will never forget our singing taxi driver!</p>
  <span class="mini-btn abs" style="left:642px">&#9757; Like</span>
  <span class="mini-btn abs" style="left:695px">&#9993; Send</span>
  <div class="likes abs"><i></i>277 people like this. Be the first of your friends.</div>
  <div class="story-btn abs">Click Here to Send Your Story</div>

  <footer class="site-footer abs">2011-12 Rovelink | Company info | Privacy Policy</footer>

</div>
</body>
</html>
```